Dalvick's Business Card

I need some designs for a new business card including the new logo attached. An old example of our business card is also attached to show all the data that should be included on the new design.
**I added some more examples someone had mocked up**

Contact Information for Business Card

Should include all info on other examples uploaded.

```html
<!DOCTYPE html>
<html lang="en">
<head>
<meta charset="utf-8">
<title>Dalvick's Business Card</title>
<link rel="stylesheet" href="https://fonts.googleapis.com/css2?family=Oswald:wght@400;500;600&display=swap">
<style>
  :root {
    --brand-blue: #0072c1;
    --brand-red: #ec1c24;
    --card-white: #ffffff;
    --backdrop: #2b2b2b;
    --text-light: #ffffff;
  }
  * { margin: 0; padding: 0; box-sizing: border-box; }
  html, body { width: 1200px; height: 1015px; overflow: hidden; }
  body {
    background: var(--backdrop);
    font-family: "Oswald", sans-serif;
    position: relative;
  }
  .card {
    position: absolute;
    left: 220px;
    width: 760px;
    height: 434px;
    background: var(--card-white);
    overflow: hidden;
    box-shadow: 0 10px 30px rgba(0,0,0,0.5);
  }
  .card--front { top: 54px; }
  .card--back { top: 528px; }
  .card__panel {
    position: absolute;
    top: 0; right: 0; bottom: 0;
    left: 348px;
    background: var(--brand-blue);
  }
  .card__band {
    position: absolute;
    left: 0; right: 0;
    top: 312px;
    height: 54px;
    background: var(--brand-red);
    color: var(--text-light);
    display: flex;
    align-items: center;
    white-space: nowrap;
  }
  .brand {
    position: absolute;
    left: 46px;
    top: 120px;
    display: flex;
    align-items: center;
    gap: 14px;
  }
  .brand__dot {
    width: 34px; height: 34px;
    border-radius: 50%;
    background: var(--brand-red);
  }
  .brand__name {
    font-weight: 600;
    font-size: 52px;
    letter-spacing: 2px;
    color: var(--brand-blue);
    line-height: 1;
  }
  .tagline {
    position: absolute;
    left: 400px;
    top: 92px;
    width: 320px;
    color: var(--text-light);
    font-weight: 500;
    font-size: 27px;
    line-height: 1.3;
    text-transform: uppercase;
  }
  .service-area {
    padding-left: 150px;
    font-weight: 600;
    font-size: 30px;
    white-space: nowrap;
  }
  .contact {
    position: absolute;
    left: 400px;
    top: 70px;
    color: var(--text-light);
  }
  .contact__name {
    font-weight: 500;
    font-size: 34px;
    text-transform: uppercase;
    line-height: 1.1;
  }
  .contact__rule {
    width: 130px;
    height: 1px;
    background: var(--text-light);
    margin: 14px 0 16px 30px;
  }
  .contact__row {
    display: flex;
    align-items: center;
    gap: 12px;
    font-size: 26px;
    line-height: 1.3;
    white-space: nowrap;
  }
  .contact__row svg { width: 22px; height: 22px; flex: none; }
  .credentials {
    padding-left: 190px;
    font-weight: 500;
    font-size: 24px;
    line-height: 1;
    text-transform: uppercase;
    gap: 22px;
  }
  .credentials span { white-space: nowrap; flex: none; }
</style>
</head>
<body>

  <section class="card card--front">
    <div class="card__panel"></div>
    <div class="brand">
      <span class="brand__dot"></span>
      <span class="brand__name">DALVICK'S</span>
    </div>
    <p class="tagline">Call today for all your HVAC, refrigeration &amp; plumbing needs</p>
    <div class="card__band">
      <p class="service-area">Serves Maple Falls, IA &amp; Surrounding Areas</p>
    </div>
  </section>

  <section class="card card--back">
    <div class="card__panel"></div>
    <div class="brand">
      <span class="brand__dot"></span>
      <span class="brand__name">DALVICK'S</span>
    </div>
    <div class="contact">
      <p class="contact__name">Mark Trelling</p>
      <div class="contact__rule"></div>
      <p class="contact__row">
        <svg viewBox="0 0 24 24" aria-hidden="true"><path fill="#fff" d="M6.6 10.8a15.1 15.1 0 0 0 6.6 6.6l2.2-2.2c.3-.3.7-.4 1-.2 1.1.4 2.3.6 3.6.6.6 0 1 .4 1 1V20c0 .6-.4 1-1 1A17 17 0 0 1 3 4c0-.6.4-1 1-1h3.5c.6 0 1 .4 1 1 0 1.3.2 2.5.6 3.6.1.3 0 .7-.2 1z"/></svg>
        555.014.2276
      </p>
      <p class="contact__row">
        <svg viewBox="0 0 24 24" aria-hidden="true"><path fill="#fff" d="M2 5h20v14H2z"/><path fill="none" stroke="#0072c1" stroke-width="1.6" d="M2 5l10 8 10-8"/></svg>
        service@dalvickhvac.com
      </p>
    </div>
    <div class="card__band credentials">
      <span>Licensed &amp; Insured</span>
      <span>|</span>
      <span>Family Owned &amp; Operated</span>
    </div>
  </section>

</body>
</html>
```